Design a Job Application & CV

I need a design for upcoming job applications that includes a cv. It needs to look as elegant and modern as possible as the application will be send mainly to large corporations and strategy consultancies. I have attached an application that I like for your consideration. One of the more difficult requirements is that it needs to be editable in ms office word for mac/windows.
As stated only the design is part of this project. I will fill in my content later on.
Reason: Dear Designers,
I am going to increase the budget as well as extending the deadline. I am hoping that you can improve upon the design that I have provided in the brief. If you have questions please let me know.
Dear Designers,
Target Market(s)
Human Resources Managers, Senior Consultants and Executives of larger firms
Industry/Entity Type
Office
Requirements
Must have
- 4 Pages including( a cover page, a coverletter page, 2 pages cv)
It should be easy to edit and should be readable by word for mac, i.e. in the *.docx format.
Here is an example of what I like:
http://www.torvenmald.example/applicationexample.pdf
http://www.torvenmald.example/applicationExample.docx
colors that I like are blue, grey, black, white
Nice to have
- icons to indicate sections
Should not have
- invasive cliparts

```html
<!DOCTYPE html>
<html lang="en">
<head>
<meta charset="utf-8">
<title>Experiences</title>
<link rel="stylesheet" href="https://fonts.googleapis.com/css2?family=Quicksand:wght@400;500&display=swap">
<style>
  :root {
    --blue: #0aa3e0;
    --charcoal: #3a3a3a;
    --graphite: #6e6e6e;
    --text: #555555;
    --paper: #ffffff;
  }
  html, body {
    margin: 0;
    padding: 0;
    overflow: hidden;
    background: var(--paper);
  }
  .page {
    position: relative;
    width: 848px;
    height: 1200px;
    overflow: hidden;
    background: var(--paper);
    font-family: "Quicksand", sans-serif;
    color: var(--text);
  }
  .top-strip, .bottom-strip {
    position: absolute;
    left: 0;
    width: 100%;
    height: 22px;
    background: linear-gradient(90deg, var(--charcoal), var(--graphite) 50%, var(--charcoal));
  }
  .top-strip { top: 0; }
  .bottom-strip { bottom: 0; }
  .header-band {
    position: absolute;
    top: 22px;
    left: 0;
    width: 100%;
    height: 157px;
    background: var(--blue);
  }
  .header-band::before {
    content: "";
    position: absolute;
    top: 28px;
    left: 0;
    right: 0;
    border-top: 2px dotted var(--paper);
  }
  .section-title {
    position: absolute;
    left: 46px;
    top: 50px;
    margin: 0;
    font-weight: 400;
    font-size: 74px;
    line-height: 1;
    color: var(--paper);
    letter-spacing: -0.5px;
  }
  .footer-band {
    position: absolute;
    bottom: 22px;
    left: 0;
    width: 100%;
    height: 27px;
    background: var(--blue);
  }
  .entry {
    position: absolute;
    left: 56px;
    width: 760px;
  }
  .entry-dates {
    font-size: 19px;
    line-height: 30px;
    color: var(--blue);
    font-weight: 500;
  }
  .entry-rule {
    margin: 6px 0 14px;
    border-top: 2px dashed var(--blue);
  }
  .entry-employer {
    margin: 0 0 6px;
    font-size: 19px;
    line-height: 30px;
    font-weight: 500;
    text-transform: uppercase;
    color: var(--text);
  }
  .entry-description {
    margin: 0;
    font-size: 18.5px;
    line-height: 42px;
    font-weight: 500;
    color: var(--text);
    width: 748px;
  }
</style>
</head>
<body>
<div class="page">
  <div class="top-strip"></div>
  <header class="header-band">
    <h1 class="section-title">Experiences</h1>
  </header>

  <section class="entry" style="top: 228px;">
    <div class="entry-dates">2003 – 2004</div>
    <div class="entry-rule"></div>
    <h2 class="entry-employer">Kestrel Build Contractors, Melbourne, Australia</h2>
    <p class="entry-description">Assistant Engineer Secured work experience as an Assistant Engineer reporting directly to the Project Manager. Liased with Engineers and reported to Project Manager on all tasks. Conducted demolition work which included working with dangerous chemicals such as asbestos. Completed survey work using laser instruments. Ensured health &amp; safety procedures were adhered to and reported any breaches.</p>
  </section>

  <section class="entry" style="top: 573px;">
    <div class="entry-dates">2002 - 2003</div>
    <div class="entry-rule"></div>
    <h2 class="entry-employer">Halvorsen Electronic Design Services, Cork</h2>
    <p class="entry-description">Trainee Engineer Reported to the Senior Engineer. Assisted with designing and building of web pages. Liaised with Engineering staff on all aspects of web content relevant to the Industry sector. Trained on PageCraft Editor for web design. Reported on progress at weekly team meetings.</p>
  </section>

  <section class="entry" style="top: 876px;">
    <div class="entry-dates">1999 - 2002</div>
    <div class="entry-rule"></div>
    <h2 class="entry-employer">Harbourside University College</h2>
    <p class="entry-description">Information Assistant, Riverside Sports Arena Checked membership cards at the Information desk. Provided assistance and information to customers. Collected money for aerobics and yoga classes. Managed special group bookings of facilities.</p>
  </section>

  <div class="footer-band"></div>
  <div class="bottom-strip"></div>
</div>
</body>
</html>
```